Business Card Design - Amberfield Court

We are looking at a new design for our business cards that has a modern and professional look. We run a residential aged care facility focussing on the care of residents. The cards will be used for potential clients, consultants and business opportunities in this sector. Blue and white is our main colours and would to see these colours incorporated in the design.
Industry/Entity Type
Business
Contact Information for Business Card
Amberfield Court, Darren Walsh, dwalsh@amberfieldcourt.com.au, Finance Manager, 0472 639 208, BCom, 37 Marrabel Crescent, Brindle Vale, Qld 4093.
Look and feel
Each slider illustrates characteristics of the customer's brand and the style your logo design should communicate.

```html
<!DOCTYPE html>
<html lang="en">
<head>
<meta charset="utf-8">
<title>Amberfield Court – Business Card</title>
<link rel="stylesheet" href="https://fonts.googleapis.com/css2?family=Open+Sans:ital,wght@0,300;0,400;0,700;1,400&display=swap">
<style>
  :root {
    --page-bg: #e9e7e3;
    --card-black: #0b0c0d;
    --card-edge: #1c1e20;
    --brand-blue: #7fb4cc;
    --brand-blue-soft: #a9cfdf;
    --text-white: #f1f3f4;
    --rule-grey: #3a3d40;
  }
  * { box-sizing: border-box; margin: 0; padding: 0; }
  html, body {
    width: 1200px; height: 1023px; overflow: hidden;
    background: var(--page-bg);
    font-family: "Open Sans", Arial, sans-serif;
  }
  .canvas { position: relative; width: 1200px; height: 1023px; }

  .card {
    position: absolute;
    width: 620px; height: 376px;
    background: linear-gradient(160deg, #1a1c1e 0%, var(--card-black) 55%);
    border: 1px solid var(--card-edge);
    border-radius: 4px;
    box-shadow: 0 14px 30px rgba(0,0,0,.35);
    color: var(--text-white);
  }

  /* Front */
  .card-front { left: 70px; top: 100px; }
  .front-brand {
    position: absolute; left: 40px; top: 0; bottom: 0; width: 270px;
    display: flex; flex-direction: column; justify-content: center;
  }
  .brand-lockup { display: flex; align-items: center; gap: 14px; }
  .brand-dot {
    width: 46px; height: 46px; border-radius: 50%;
    background: var(--brand-blue); flex: none;
  }
  .brand-name {
    font-weight: 300; font-size: 26px; letter-spacing: 2px;
    text-transform: uppercase; color: var(--brand-blue); line-height: 1.15;
  }
  .brand-tagline {
    margin-top: 14px; margin-left: 60px;
    font-style: italic; font-size: 14px; color: var(--text-white);
  }
  .front-divider {
    position: absolute; left: 330px; top: 60px; bottom: 60px;
    width: 1px; background: var(--rule-grey);
  }
  .front-contact {
    position: absolute; left: 360px; top: 0; bottom: 0; right: 24px;
    display: flex; flex-direction: column; justify-content: center;
  }
  .person-name {
    font-weight: 700; font-size: 24px; letter-spacing: .5px;
    color: var(--brand-blue); text-transform: uppercase;
  }
  .person-role {
    font-size: 12px; text-transform: uppercase; margin: 4px 0 12px;
    letter-spacing: .4px;
  }
  .contact-line {
    display: flex; align-items: center; gap: 8px;
    font-size: 12.5px; line-height: 1.9;
  }
  .contact-icon { width: 13px; height: 13px; flex: none; }
  .address-line {
    font-size: 12.5px; line-height: 1.8; text-transform: uppercase;
    letter-spacing: .3px;
  }
  .address-line:first-of-type { margin-top: 4px; }

  /* Back */
  .card-back { left: 510px; top: 560px; }
  .back-content {
    position: absolute; left: 56px; top: 100px;
  }
  .back-name {
    font-weight: 300; font-size: 40px; letter-spacing: 4px;
    text-transform: uppercase; color: var(--brand-blue-soft);
  }
  .back-tagline {
    font-style: italic; font-size: 22px; color: var(--text-white);
    margin-top: 6px;
  }
</style>
</head>
<body>
<main class="canvas">

  <section class="card card-front" aria-label="Business card front">
    <div class="front-brand">
      <div class="brand-lockup">
        <span class="brand-dot"></span>
        <span class="brand-name">Amberfield Court</span>
      </div>
      <p class="brand-tagline">Respect, Warmth, Belonging</p>
    </div>

    <div class="front-divider"></div>

    <div class="front-contact">
      <h1 class="person-name">Darren Walsh</h1>
      <p class="person-role">Finance Manager</p>
      <p class="contact-line">
        <svg class="contact-icon" viewBox="0 0 16 16" aria-hidden="true">
          <rect x="0" y="0" width="16" height="16" rx="3" fill="#7fb4cc"/>
          <rect x="5" y="3" width="6" height="10" rx="1" fill="#0b0c0d"/>
        </svg>
        0472 639 208
      </p>
      <p class="contact-line">
        <svg class="contact-icon" viewBox="0 0 16 16" aria-hidden="true">
          <rect x="0" y="0" width="16" height="16" rx="3" fill="#7fb4cc"/>
          <rect x="3" y="5" width="10" height="7" fill="#0b0c0d"/>
          <path d="M3 5 L8 9 L13 5" stroke="#7fb4cc" stroke-width="1.2" fill="none"/>
        </svg>
        dwalsh@amberfieldcourt.com.au
      </p>
      <p class="address-line">BCom, 37 Marrabel Crescent</p>
      <p class="address-line">Brindle Vale, Qld 4093.</p>
    </div>
  </section>

  <section class="card card-back" aria-label="Business card back">
    <div class="back-content">
      <h2 class="back-name">Amberfield Court</h2>
      <p class="back-tagline">Respect, Warmth, Belonging</p>
    </div>
  </section>

</main>
</body>
</html>
```